Stylish Business Cards Wanted

- DOUBLE SIDED Design Required -

High end, edgy cards for a corporate and personal stylist. Must include logo,
Name: Belinda Harwick
Title: Director and Stylist
telephone : +61 8 7142 5809
email: belinda@theloombriefing.example
website: theloombriefing.example
Tag: Corporate Workwear & Uniform Specialist | Personal Stylist
Would like nice icons for telephone, email, website

Target Market(s)

Businesses wanting stylish uniforms, people wanting stylish wardrobes

Industry/Entity Type

Corporate Workwear Stylist

Contact Information for Business Card

I would like black, white and gold foiling incorporated in the design - possibly a touch of the other colours on my branding guide attached Name: Belinda Harwick Title: Director and Stylist telephone : +61 8 7142 5809 email: belinda@theloombriefing.example website: theloombriefing.example Tag: Corporate Workwear & Uniform Specialist | Personal Stylist Would like nice icons for telephone, email, website

Font styles to use
Other font styles liked:
• Raleway

Colors

Designer to choose colors to be used in the design.

Requirements
Must have
• Gold foil accents

```html
<!DOCTYPE html>
<html lang="en">
<head>
<meta charset="utf-8">
<title>The Loom Briefing — Business Card</title>
<link href="https://fonts.googleapis.com/css2?family=Open+Sans:wght@400;600;700&display=swap" rel="stylesheet">
<style>
  :root {
    --backdrop: #3b3b3c;
    --card: #151515;
    --gold: #cfc08a;
    --gold-soft: #b9ab78;
    --gold-edge: #d8c98f;
  }
  * { margin: 0; padding: 0; box-sizing: border-box; }
  html, body {
    width: 1200px; height: 801px; overflow: hidden;
    background: var(--backdrop);
    font-family: "Open Sans", Arial, sans-serif;
  }
  .canvas {
    width: 1200px; height: 801px;
    display: flex; align-items: center; justify-content: center; gap: 40px;
  }
  .card {
    position: relative;
    width: 540px; height: 310px;
    background: var(--card);
    border: 1.5px solid var(--gold-edge);
    color: var(--gold);
  }

  /* Contact side */
  .card-contact {
    display: flex; align-items: center;
    padding: 0 36px 0 40px;
  }
  .identity { width: 220px; text-align: right; padding-right: 22px; }
  .identity-name {
    font-weight: 700; font-size: 19px; letter-spacing: 0.04em;
    text-transform: uppercase;
  }
  .identity-title { font-size: 14px; color: var(--gold-soft); margin-top: 3px; }
  .divider { width: 1px; height: 62px; background: var(--gold-soft); }
  .contact-list { list-style: none; padding-left: 22px; }
  .contact-item {
    display: flex; align-items: center; gap: 8px;
    font-size: 13.5px; line-height: 1.75;
  }
  .contact-icon { width: 13px; height: 13px; flex: none; }

  /* Brand side */
  .card-brand {
    display: flex; flex-direction: column; align-items: center; justify-content: center;
  }
  .brand-name {
    display: flex; align-items: center; gap: 12px;
    font-weight: 700; font-size: 38px; letter-spacing: 0.02em;
    color: var(--gold);
    margin-top: -20px;
  }
  .brand-dot { width: 14px; height: 14px; border-radius: 50%; background: var(--gold); }
  .tagline {
    position: absolute; left: 0; right: 0; bottom: 36px;
    text-align: center; font-size: 14.5px; color: var(--gold-soft);
  }
  .tagline-sep { margin: 0 10px; }
</style>
</head>
<body>
<main class="canvas">
  <section class="card card-contact" aria-label="Contact side">
    <div class="identity">
      <p class="identity-name">Belinda Harwick</p>
      <p class="identity-title">Director and Stylist</p>
    </div>
    <span class="divider"></span>
    <ul class="contact-list">
      <li class="contact-item">
        <svg class="contact-icon" viewBox="0 0 16 16" aria-hidden="true">
          <circle cx="8" cy="8" r="8" fill="var(--gold)"/>
          <path d="M5.3 4.2l1.4 1.6-.7 1c.5 1.1 1.3 1.9 2.4 2.4l1-.7 1.6 1.4-.6 1.1c-3 0-5.7-2.7-5.7-5.7z" fill="var(--card)"/>
        </svg>
        +61 8 7142 5809
      </li>
      <li class="contact-item">
        <svg class="contact-icon" viewBox="0 0 16 16" aria-hidden="true">
          <circle cx="8" cy="8" r="8" fill="var(--gold)"/>
          <rect x="4" y="5.3" width="8" height="5.4" fill="var(--card)"/>
          <path d="M4 5.3l4 3 4-3" stroke="var(--gold)" stroke-width="0.9" fill="none"/>
        </svg>
        belinda@theloombriefing.example
      </li>
      <li class="contact-item">
        <svg class="contact-icon" viewBox="0 0 16 16" aria-hidden="true">
          <circle cx="8" cy="8" r="8" fill="var(--gold)"/>
          <g stroke="var(--card)" stroke-width="1" fill="none">
            <circle cx="8" cy="8" r="4.2"/>
            <ellipse cx="8" cy="8" rx="1.8" ry="4.2"/>
            <path d="M3.8 8h8.4"/>
          </g>
        </svg>
        theloombriefing.example
      </li>
    </ul>
  </section>

  <section class="card card-brand" aria-label="Brand side">
    <p class="brand-name"><span class="brand-dot" aria-hidden="true"></span>The Loom Briefing</p>
    <p class="tagline">Corporate Workwear &amp; Uniform Specialist<span class="tagline-sep">•</span>Personal Stylist</p>
  </section>
</main>
</body>
</html>
```